We are a recruitment company based in Norwich/Cambridge England.
I have included our company logo which we want to remain the same.

What we are looking for is a new creative Business card which will really stand out!!

Contact Information for Business Card

Harriet Dunmore
email: Harriet@plavex.co.uk
Address: Brackwell House
Fenmoor Enterprise Park
Partridge Way
Norwich
QB9 3KX
Tel:01632 960418

```html
<!DOCTYPE html>
<html lang="en">
<head>
<meta charset="utf-8">
<title>Plavex Business Card</title>
<link href="https://fonts.googleapis.com/css2?family=Jost:wght@300;400;500&family=Oswald:wght@500&display=swap" rel="stylesheet">
<style>
  :root {
    --backdrop-light: #4a4a4a;
    --backdrop-dark: #1e1e1e;
    --card: #1c1c1c;
    --card-edge: #262626;
    --ink: #f2f2f2;
    --ink-soft: #bdbdbd;
    --ink-muted: #8a8a8a;
    --accent: #8dc63f;
  }
  * { margin: 0; padding: 0; box-sizing: border-box; }
  html, body { width: 1200px; height: 900px; overflow: hidden; }
  body {
    background: radial-gradient(ellipse at 70% 15%, var(--backdrop-light), var(--backdrop-dark) 75%);
    font-family: "Jost", sans-serif;
    color: var(--ink);
    position: relative;
  }
  .card {
    position: absolute;
    left: 220px;
    width: 760px;
    height: 400px;
    background: linear-gradient(160deg, var(--card-edge), var(--card) 60%);
    box-shadow: 0 18px 40px rgba(0,0,0,0.55);
  }
  .card--front { top: 35px; }
  .card--back { top: 465px; }

  .brand {
    position: absolute;
    top: 130px;
    left: 0; right: 0;
    display: flex;
    flex-direction: column;
    align-items: center;
  }
  .brand__row { display: flex; align-items: center; gap: 18px; }
  .brand__dot {
    width: 58px; height: 58px; border-radius: 50%;
    background: #111;
    box-shadow: inset 0 2px 3px rgba(255,255,255,0.06);
  }
  .brand__name {
    font-family: "Jost", sans-serif;
    font-weight: 500;
    font-size: 62px;
    color: var(--ink-soft);
    line-height: 1;
  }
  .brand__tagline {
    margin-top: 6px;
    margin-left: 76px;
    font-size: 10px;
    letter-spacing: 5px;
    color: var(--ink-muted);
  }
  .web {
    letter-spacing: 4px;
    font-weight: 300;
  }
  .web em { font-style: normal; color: var(--accent); font-weight: 400; }
  .card--front .web {
    position: absolute;
    bottom: 40px; left: 0; right: 0;
    text-align: center;
    font-size: 16px;
    color: var(--ink-soft);
  }

  .identity {
    position: absolute;
    top: 140px;
    right: 430px;
    text-align: right;
  }
  .identity__name {
    font-family: "Oswald", sans-serif;
    font-weight: 500;
    font-size: 44px;
    line-height: 1;
    text-transform: uppercase;
    letter-spacing: 0.5px;
  }
  .identity__role {
    font-weight: 300;
    font-size: 24px;
    text-transform: uppercase;
    margin-top: 4px;
  }
  .divider {
    position: absolute;
    top: 140px;
    left: 350px;
    width: 2px;
    height: 82px;
    background: var(--ink);
  }
  .contacts {
    position: absolute;
    top: 142px;
    left: 372px;
    list-style: none;
    font-size: 20px;
    font-weight: 400;
    line-height: 27px;
  }
  .contacts li { display: flex; align-items: center; gap: 12px; }
  .contacts svg { width: 18px; height: 18px; flex: none; }
  .contacts .web { letter-spacing: 1px; font-size: 20px; }
  .address {
    position: absolute;
    bottom: 55px;
    left: 0; right: 0;
    text-align: center;
    font-size: 20px;
    letter-spacing: 0.5px;
  }
</style>
</head>
<body>
  <section class="card card--front">
    <div class="brand">
      <div class="brand__row">
        <span class="brand__dot"></span>
        <span class="brand__name">Plavex</span>
      </div>
      <span class="brand__tagline">Technology Recruitment</span>
    </div>
    <p class="web">www.<em>plavexrecruit</em>.com</p>
  </section>

  <section class="card card--back">
    <div class="identity">
      <h1 class="identity__name">Harriet Dunmore</h1>
      <p class="identity__role">CEO &amp; Founder</p>
    </div>
    <span class="divider"></span>
    <ul class="contacts">
      <li>
        <svg viewBox="0 0 24 24" aria-hidden="true"><path fill="var(--accent)" d="M6.6 10.8a15 15 0 0 0 6.6 6.6l2.2-2.2a1 1 0 0 1 1-.25 11.4 11.4 0 0 0 3.6.57 1 1 0 0 1 1 1V20a1 1 0 0 1-1 1A17 17 0 0 1 3 4a1 1 0 0 1 1-1h3.5a1 1 0 0 1 1 1c0 1.25.2 2.45.57 3.57a1 1 0 0 1-.25 1z"/></svg>
        <span>01632 960418</span>
      </li>
      <li>
        <svg viewBox="0 0 24 24" aria-hidden="true"><rect x="2" y="5" width="20" height="14" rx="1.5" fill="var(--accent)"/><path d="M2.5 6l9.5 7 9.5-7" fill="none" stroke="var(--card)" stroke-width="1.6"/></svg>
        <span>harriet@plavex.co.uk</span>
      </li>
      <li>
        <svg viewBox="0 0 24 24" aria-hidden="true"><circle cx="14" cy="10" r="6.5" fill="none" stroke="var(--accent)" stroke-width="2.4"/><path d="M9.3 14.7 3 21" stroke="var(--accent)" stroke-width="2.8" stroke-linecap="round"/></svg>
        <span class="web">www.<em>plavexrecruit</em>.com</span>
      </li>
    </ul>
    <p class="address">Brackwell House Fenmoor Enterprise Park, Partridge Way Norwich, QB9 3KX</p>
  </section>
</body>
</html>
```